Travel Agency Website - Simple General

Need a 7 page simple design that is pretty repetitive. Need to be able to load quickly that is SEO optimized. Trying to give ideas on what they can do, be personal as we are local, but at the same time come across as professional and get information easily with little burden.

- Landing Page
- Brimwell Vacations Page
- Family Trips
- Road Trips from Texas
- Other Destinations
- About Us Page
- Contact Us Page

Target Market(s)

Families

Coding

Coded - Design and coding required

Number of Pages Required

5+ page

Colors

Designer to choose colors to be used in the design.

Requirements
Must have
• Like it to flow easily with our logo. Use that for colors, etc.

```html
<!DOCTYPE html>
<html lang="en">
<head>
<meta charset="utf-8">
<title>Roamwell Travel – Texas Road Trips</title>
<link rel="stylesheet" href="https://fonts.googleapis.com/css2?family=Outfit:wght@400;500;700&display=swap">
<style>
  :root {
    --teal-dark: #1d4f5c;
    --teal: #2a8a8a;
    --teal-footer: #268080;
    --gold: #c4974a;
    --white: #ffffff;
    --bar: rgba(255,255,255,0.94);
    --card: rgba(244,247,248,0.86);
    --card-line: #5fb4b0;
  }
  * { box-sizing: border-box; margin: 0; padding: 0; }
  html, body { width: 1200px; height: 847px; overflow: hidden; }
  body { font-family: "Outfit", sans-serif; color: var(--teal-dark); position: relative; }

  .hero-photo {
    position: absolute; inset: 0 0 59px 0;
    background: linear-gradient(180deg, #2f7fd4 0%, #7fb6e6 22%, #b9d3ea 33%, #d9733a 44%, #b8612c 52%, #4f7330 62%, #7b8070 74%, #d2652a 88%, #c4802f 100%);
  }

  .contact-row { position: absolute; top: 19px; left: 570px; display: flex; gap: 34px; font-size: 15px; font-weight: 500; color: var(--white); }
  .contact-item { display: flex; align-items: center; gap: 7px; }
  .contact-icon { width: 26px; height: 26px; border-radius: 50%; background: var(--white); display: flex; align-items: center; justify-content: center; }

  .nav-bar {
    position: absolute; left: 270px; top: 66px; width: 870px; height: 59px;
    background: var(--bar); border-radius: 0 30px 30px 0;
    display: flex; align-items: center; padding-left: 28px; font-size: 16px;
  }
  .nav-home { margin-right: 16px; display: flex; }
  .nav-links { display: flex; list-style: none; }
  .nav-links li { margin-right: 24px; white-space: nowrap; }
  .nav-links li.about { margin-left: 12px; }
  .contact-btn {
    position: absolute; left: 711px; top: 9px; width: 144px; height: 39px;
    background: var(--gold); color: var(--white); border-radius: 20px;
    display: flex; align-items: center; padding-left: 29px; font-size: 14.5px;
  }
  .contact-btn .arrow { position: absolute; right: 7px; top: 6px; width: 27px; height: 27px; border-radius: 50%; background: #d8ad63; display: flex; align-items: center; justify-content: center; }

  .brand {
    position: absolute; left: 80px; top: 60px; width: 190px; height: 70px;
    display: flex; align-items: center; justify-content: center; gap: 8px;
    background: var(--white); border-radius: 14px;
    font-size: 22px; font-weight: 700; color: var(--teal-dark);
  }
  .brand-dot { width: 14px; height: 14px; border-radius: 50%; background: var(--teal); }

  .hero-card { position: absolute; left: 70px; top: 210px; width: 470px; height: 420px; }
  .hero-card svg { position: absolute; inset: 0; }
  .hero-content { position: absolute; inset: 0; text-align: center; }
  .hero-title { position: absolute; top: 113px; width: 100%; font-weight: 700; font-size: 38px; line-height: 37px; letter-spacing: 0.5px; }
  .hero-title .line-1 { display: block; color: var(--teal-dark); }
  .hero-title .line-2 { display: block; color: var(--teal); }
  .hero-text { position: absolute; top: 202px; left: 70px; width: 330px; font-size: 16.5px; line-height: 19.5px; color: var(--teal-dark); }
  .hero-btn {
    position: absolute; left: 155px; top: 283px; width: 168px; height: 39px;
    background: var(--gold); color: var(--white); font-size: 13px; font-weight: 700;
    display: flex; align-items: center; justify-content: center; letter-spacing: 0.3px;
  }

  .site-footer {
    position: absolute; left: 0; bottom: 0; width: 1200px; height: 59px;
    background: var(--teal-footer); color: var(--white); font-size: 14px;
  }
  .site-footer p { position: absolute; left: 0; width: 1155px; text-align: center; top: 20px; }
  .social { position: absolute; top: 17px; left: 1042px; display: flex; gap: 7px; }
  .social span { width: 24px; height: 24px; border-radius: 50%; background: var(--white); display: block; }
</style>
</head>
<body>
  <div class="hero-photo" role="img" aria-label="Photo of a red canyon landscape in Texas with green shrubs, dry grass and a winding road under a blue sky"></div>

  <header>
    <div class="contact-row">
      <span class="contact-item">
        <span class="contact-icon"><svg width="14" height="10" viewBox="0 0 14 10"><rect x="0.5" y="0.5" width="13" height="9" rx="1" fill="none" stroke="#2f7fd4"/><path d="M1 1l6 5 6-5" fill="none" stroke="#2f7fd4"/></svg></span>
        hello@roamwelltravel.com
      </span>
      <span class="contact-item">
        <span class="contact-icon"><svg width="13" height="13" viewBox="0 0 24 24"><path fill="#2f7fd4" d="M6.6 10.8a15 15 0 006.6 6.6l2.2-2.2a1 1 0 011-.25 11.4 11.4 0 003.6.6 1 1 0 011 1V20a1 1 0 01-1 1A17 17 0 013 4a1 1 0 011-1h3.5a1 1 0 011 1c0 1.25.2 2.45.6 3.6a1 1 0 01-.25 1z"/></svg></span>
        Phone Number (555) 214 7730
      </span>
    </div>

    <nav class="nav-bar">
      <span class="nav-home"><svg width="14" height="13" viewBox="0 0 14 13"><path d="M7 0L0 6h2v7h4V9h2v4h4V6h2z" fill="var(--gold)"/></svg></span>
      <ul class="nav-links">
        <li>Brimwell Vacations</li>
        <li>Family Trips</li>
        <li>Texas Road Trips</li>
        <li>Other Destinations</li>
        <li class="about">About Us</li>
      </ul>
      <a class="contact-btn">Contact Us
        <span class="arrow"><svg width="10" height="10" viewBox="0 0 10 10"><path d="M2 8L8 2M3.5 2H8v4.5" fill="none" stroke="#fff" stroke-width="1.4"/></svg></span>
      </a>
    </nav>

    <div class="brand"><span class="brand-dot"></span>Roamwell Travel</div>
  </header>

  <main>
    <section class="hero-card">
      <svg viewBox="0 0 470 420" width="470" height="420" aria-hidden="true">
        <path d="M235 0C255 18 285 28 330 30C395 33 420 55 425 100C428 130 450 150 470 210C450 270 428 290 425 320C420 365 395 387 330 390C285 392 255 402 235 420C215 402 185 392 140 390C75 387 50 365 45 320C42 290 20 270 0 210C20 150 42 130 45 100C50 55 75 33 140 30C185 28 215 18 235 0Z" fill="var(--card)"/>
        <path transform="translate(235 210) scale(0.93) translate(-235 -210)" d="M235 0C255 18 285 28 330 30C395 33 420 55 425 100C428 130 450 150 470 210C450 270 428 290 425 320C420 365 395 387 330 390C285 392 255 402 235 420C215 402 185 392 140 390C75 387 50 365 45 320C42 290 20 270 0 210C20 150 42 130 45 100C50 55 75 33 140 30C185 28 215 18 235 0Z" fill="none" stroke="var(--card-line)" stroke-width="2"/>
      </svg>
      <div class="hero-content">
        <h1 class="hero-title"><span class="line-1">TEXAS ROAD TRIPS</span><span class="line-2">MADE EASY</span></h1>
        <p class="hero-text">tress-free, fun-filled vacations designed for all ages—because every family deserves time together.</p>
        <a class="hero-btn">PLAN FAMILY TRIP</a>
      </div>
    </section>
  </main>

  <footer class="site-footer">
    <p>© 2026 Roamwell Travel. All Right Reserved</p>
    <div class="social"><span></span><span></span></div>
  </footer>
</body>
</html>
```